Create a proposal + product powerpoint

Please see the powerpoint for the slides. There are about 20 slides to be created. Rest of them are for reference and show the design that I like.

I would like to move fast on this, since I need to present it next week (in the week of April 21st).

Please download the current content from here:
https://www.parcelbrook.net/fetch/qRtVmXzLwPkNbYcD

Please make at least 4 slides with the specific content so I can assess your design style.

Target Market(s)

Business Audience and very senior technical audience
Decision Makers

Industry/Entity Type

Product

Colors
e34297
a64599

Requirements
Must have
• Should be very clean, crisp.

I like to use Icons as shown in the powerpoint.... Please see the appendix of the slide deck that shows the various icons. Most of them just have plain text, and I would like to organize so that it does not look like some is just reading text.

I would like to focus on the design aspects so that the audience is clear on how the solution works.

Every page should some graphic element based on the slides shown in the appendix.

```html
<!DOCTYPE html>
<html lang="en">
<head>
<meta charset="utf-8">
<title>Lifecycle management solution</title>
<link rel="stylesheet" href="https://fonts.googleapis.com/css2?family=Roboto+Condensed:wght@400;500&display=swap">
<style>
  :root {
    --title: #8e1a9a;
    --rule: #d9d9d9;
    --icon-bg: #c043b2;
    --row-bg: #fdd5f6;
    --row-text: #9a1f6a;
    --footer-dark: #9a1d5c;
    --footer-light: #b14cb3;
    --deco-a: #f6d2f1;
    --deco-b: #d070d5;
    --white: #ffffff;
    --logo-text: #9a9a9a;
  }
  * { margin: 0; padding: 0; box-sizing: border-box; }
  html, body { width: 1200px; height: 900px; overflow: hidden; background: var(--white); }
  .slide {
    position: relative; width: 1200px; height: 900px; overflow: hidden;
    font-family: "Roboto Condensed", sans-serif; background: var(--white);
  }
  .glow {
    position: absolute; left: -220px; top: 420px; width: 560px; height: 420px;
    background: radial-gradient(ellipse at center, rgba(214,150,222,0.45), rgba(255,255,255,0) 70%);
  }
  .deco { position: absolute; right: 0; top: 90px; width: 300px; height: 752px; }
  .slide-title {
    position: absolute; left: 40px; top: 14px;
    font-size: 50px; font-weight: 400; color: var(--title); letter-spacing: -0.5px;
  }
  .title-rule { position: absolute; left: 40px; right: 0; top: 89px; height: 3px; background: var(--rule); }
  .logo-box {
    position: absolute; left: 1036px; top: 10px; width: 150px; height: 70px;
    border: 2px solid #ececec; border-radius: 10px; background: var(--white);
    display: flex; align-items: center; justify-content: center;
    font-size: 28px; color: var(--logo-text); letter-spacing: 1px;
  }
  .features { position: absolute; left: 44px; top: 149px; list-style: none; }
  .feature { display: flex; height: 93px; margin-bottom: 27px; }
  .feature-icon {
    width: 148px; height: 93px; background: var(--icon-bg);
    border: 3px solid var(--white); display: flex; align-items: center; justify-content: center;
  }
  .feature-icon svg { width: 72px; height: 72px; }
  .feature-label {
    width: 736px; height: 93px; margin-left: 2px; background: var(--row-bg);
    border: 3px solid var(--white); box-shadow: 0 0 0 1px #f1e0ee;
    display: flex; align-items: center; padding-left: 20px;
    font-size: 42px; color: var(--row-text); letter-spacing: 0.3px;
  }
  .footer { position: absolute; left: 0; bottom: 0; width: 1200px; height: 58px; }
  .footer-bands { position: absolute; inset: 0; }
  .page-number, .copyright {
    position: absolute; top: 0; height: 58px; display: flex; align-items: center;
    color: var(--white); font-size: 25px; letter-spacing: 0.5px;
  }
  .page-number { left: 14px; }
  .copyright { right: 14px; }
</style>
</head>
<body>
<div class="slide">
  <div class="glow"></div>

  <svg class="deco" viewBox="0 0 300 752" role="img" aria-label="Decorative background of soft purple geometric facets">
    <defs>
      <linearGradient id="decoFill" x1="0" y1="0" x2="1" y2="0.3">
        <stop offset="0" stop-color="var(--deco-a)" stop-opacity="0.4"/>
        <stop offset="0.6" stop-color="var(--deco-b)" stop-opacity="0.55"/>
        <stop offset="1" stop-color="var(--deco-b)" stop-opacity="0.85"/>
      </linearGradient>
    </defs>
    <polygon points="30,0 300,0 300,752 0,752 80,560 0,360 60,180" fill="url(#decoFill)"/>
  </svg>

  <h1 class="slide-title">Lifecycle management solution</h1>
  <div class="title-rule"></div>
  <div class="logo-box">LOGO HERE</div>

  <ul class="features">
    <li class="feature">
      <div class="feature-icon">
        <svg viewBox="0 0 72 72" fill="none" stroke="#fff" stroke-width="6" stroke-linecap="square">
          <polyline points="22,20 6,36 22,52"/><polyline points="50,20 66,36 50,52"/><line x1="42" y1="26" x2="30" y2="46"/>
        </svg>
      </div>
      <div class="feature-label">Code Promotion</div>
    </li>
    <li class="feature">
      <div class="feature-icon">
        <svg viewBox="0 0 72 72" fill="#fff">
          <circle cx="14" cy="14" r="5"/><rect x="9" y="21" width="10" height="16" rx="2"/>
          <circle cx="36" cy="10" r="5"/><rect x="31" y="17" width="10" height="18" rx="2"/>
          <circle cx="58" cy="14" r="5"/><rect x="53" y="21" width="10" height="16" rx="2"/>
          <path d="M10 60 C30 64 20 46 40 44 L62 42 L62 47 L42 49 C28 51 40 66 10 66 Z"/>
        </svg>
      </div>
      <div class="feature-label">Change Management</div>
    </li>
    <li class="feature">
      <div class="feature-icon">
        <svg viewBox="0 0 72 72" fill="none" stroke="#fff" stroke-width="8" stroke-linecap="round">
          <line x1="16" y1="16" x2="58" y2="58"/><line x1="58" y1="14" x2="16" y2="56"/>
          <circle cx="60" cy="12" r="8" stroke-width="5"/>
        </svg>
      </div>
      <div class="feature-label">Troubleshooting</div>
    </li>
    <li class="feature">
      <div class="feature-icon">
        <svg viewBox="0 0 72 72" fill="#fff">
          <path d="M12 22 H28 A8 8 0 1 1 42 22 H56 V36 A8 8 0 1 1 56 50 V64 H40 A8 8 0 1 0 28 64 H12 V50 A8 8 0 1 0 12 36 Z"/>
        </svg>
      </div>
      <div class="feature-label">Build and test automation</div>
    </li>
    <li class="feature">
      <div class="feature-icon">
        <svg viewBox="0 0 72 72" fill="#fff">
          <rect x="8" y="52" width="9" height="16"/><rect x="22" y="44" width="9" height="24"/>
          <rect x="36" y="34" width="9" height="34"/><rect x="50" y="24" width="9" height="44"/>
          <polyline points="4,42 22,28 34,32 60,8" fill="none" stroke="#fff" stroke-width="3"/>
          <polygon points="64,4 54,6 62,14"/>
        </svg>
      </div>
      <div class="feature-label">Audit Analysis</div>
    </li>
  </ul>

  <footer class="footer">
    <svg class="footer-bands" viewBox="0 0 1200 58" preserveAspectRatio="none">
      <polygon points="0,0 906,0 940,58 0,58" fill="var(--footer-dark)"/>
      <polygon points="920,0 1200,0 1200,58 954,58" fill="var(--footer-light)"/>
    </svg>
    <span class="page-number">Page : 01</span>
    <span class="copyright">Copyright text here</span>
  </footer>
</div>
</body>
</html>
```